Modern Verdell Tree Care Website

I need a website for a full service Tree Care company. The company provides tree pruning, tree removal, tree preservation, emergency services, stump grinding, and emergency tree services.

Target Market(s)

Customers that need tree services

Industry/Entity Type

Landscaping, Tree Services

Coding

Coded - Design and coding required

Number of Pages Required

5+ page

Font styles to use
Sans Serif

Requirements
Must have
• Good clean design that showcases the services the company provides.
Nice to have
• Services page; contact form, blog, home page, about page

```html
<!DOCTYPE html>
<html lang="en">
<head>
<meta charset="utf-8">
<title>Verdell Tree Care</title>
<link href="https://fonts.googleapis.com/css2?family=Montserrat:wght@400;500;600;700;800&display=swap" rel="stylesheet">
<style>
:root{
  --green:#7fbf3a;
  --green-dark:#5e9a26;
  --orange:#f7a535;
  --ink:#1f1f1f;
  --text:#444;
  --cream:#f1efe6;
  --white:#fff;
}
*{box-sizing:border-box;margin:0;padding:0}
html,body{width:1200px;height:4839px;overflow:hidden}
body{font-family:'Montserrat',sans-serif;color:var(--ink);background:var(--white);position:relative}
.abs{position:absolute}
.ph{position:absolute}
/* header */
.site-header{position:absolute;top:0;left:0;width:1200px;height:80px;background:#fff;display:flex;align-items:center;padding:0 96px;border-bottom:1px solid #eee}
.brand{display:flex;align-items:center;gap:10px;font-weight:800;font-size:24px;color:var(--green-dark);letter-spacing:1px}
.brand-mark{width:22px;height:22px;background:var(--green)}
.main-nav{display:flex;gap:42px;margin-left:auto;font-size:12px;font-weight:600}
.main-nav a{color:var(--ink);text-decoration:none}
.main-nav a.active{color:var(--green);border-bottom:2px solid var(--green);padding-bottom:6px}
.phone-pill{margin-left:22px;background:var(--green);color:#fff;border-radius:24px;padding:10px 20px;font-size:13px;font-weight:600;display:flex;align-items:center;gap:8px}
.phone-ico{width:22px;height:22px;border-radius:50%;background:#fff;display:flex;align-items:center;justify-content:center}
/* hero */
.hero{position:absolute;top:80px;left:0;width:1200px;height:638px;overflow:hidden}
.hero-copy{position:absolute;left:108px;top:186px;color:#fff}
.hero-copy .eyebrow{font-size:17px;letter-spacing:1px}
.hero-copy h1{font-size:38px;font-weight:800;line-height:1.18;margin:14px 0 16px}
.hero-copy p{font-size:17px}
.btn{display:inline-block;border-radius:30px;color:#fff;font-weight:700;font-size:14px;text-transform:uppercase;padding:14px 34px}
.btn-orange{background:var(--orange)}
.btn-green{background:var(--green)}
/* about */
.about-text{position:absolute;left:610px;top:828px;width:515px}
.sec-title{font-size:34px;font-weight:800;line-height:1.15}
.sec-title span{font-weight:400;color:var(--green)}
.about-text .sec-title span{display:block}
.rule{width:72px;height:3px;background:linear-gradient(90deg,var(--orange) 50%,var(--green) 50%);margin:10px 0 0}
.about-text p{font-size:14.5px;line-height:1.6;color:var(--text);margin-top:22px;padding-left:10px}
.about-text p.quote{border-left:2px solid var(--orange);padding-left:18px;margin-left:8px}
/* services */
.services{position:absolute;top:1350px;left:0;width:1200px;height:690px;background:var(--cream)}
.center-title{position:absolute;width:1200px;text-align:center}
.center-title .rule{margin:10px auto 0}
.svc{position:absolute;width:302px;height:216px;border-radius:0 26px 0 26px;overflow:hidden;display:flex;align-items:flex-end;justify-content:center;color:#fff;font-weight:700;font-size:17px;padding-bottom:26px}
.svc::after{content:"";position:absolute;bottom:14px;left:50%;width:34px;height:2px;background:#fff;margin-left:-17px}
.svc span{position:relative;z-index:1}
.svc.featured{background:#2f5b22;flex-direction:column;justify-content:center;padding:0 40px;text-align:center}
.svc.featured p{font-size:11px;font-weight:400;line-height:1.5;margin:10px 0 12px}
.svc.featured .mini{background:var(--green);border-radius:14px;font-size:9px;padding:6px 18px}
.svc.featured::after{display:none}
/* why */
.feature{position:absolute;display:flex;align-items:center;gap:16px;font-size:14px;font-weight:700;line-height:1.35}
.dot-ico{width:76px;height:76px;border-radius:50%;display:flex;align-items:center;justify-content:center;flex:none}
.dot-ico.g{background:var(--green)} .dot-ico.o{background:var(--orange)}
/* blogs */
.blogs{position:absolute;top:2776px;left:0;width:1200px;height:642px;background:var(--cream)}
.card{position:absolute;background:#fff;border:1px solid #ddd}
.tag{display:inline-block;background:var(--green);color:#fff;font-size:11px;font-weight:600;padding:5px 14px}
.card h3{font-size:17px;font-weight:600;line-height:1.45}
.more{color:var(--green);font-size:12px;font-weight:700;text-decoration:underline;display:block;margin-top:8px}
/* testimonials */
.testi{position:absolute;top:3418px;left:0;width:1200px;height:512px;overflow:hidden}
.bubble{position:absolute;width:330px;height:330px;border-radius:50%;background:#fff;border:3px solid var(--green);box-shadow:0 0 0 12px #f4f4f4;text-align:center;padding:46px 44px;font-size:12.5px;line-height:1.65;color:var(--text)}
.bubble .q{font-size:46px;color:var(--orange);font-weight:800;line-height:1}
.bubble b{display:block;color:var(--ink);font-size:14px;margin-top:8px}
.stars{color:var(--orange);font-size:20px;letter-spacing:2px}
/* contact */
.field{position:absolute;left:138px;width:414px;height:44px;border:1px solid #ccc;background:#fff;font-size:12px;padding:14px 22px;color:#333}
/* footer */
.footer-nav{position:absolute;top:4640px;left:106px;width:994px;height:52px;border-top:1px solid #ccc;border-bottom:1px solid #ccc;display:flex;justify-content:space-around;align-items:center;font-size:14px;font-weight:600}
.footer-nav i{width:5px;height:5px;border-radius:50%;background:var(--green)}
.f-contact{position:absolute;top:4720px;display:flex;align-items:center;gap:10px;font-size:13px;font-weight:600}
.copyright{position:absolute;top:4800px;left:0;width:1200px;height:39px;background:#f3f3f3;text-align:center;font-size:12px;line-height:39px;color:#444}
</style>
</head>
<body>

<header class="site-header">
  <div class="brand"><span class="brand-mark"></span>Verdell Tree Care</div>
  <nav class="main-nav">
    <a class="active">HOME</a><a>ABOUT US</a><a>SERVICES</a><a>BLOG</a><a>REVIEW</a><a>CONTACT US</a>
  </nav>
  <div class="phone-pill"><span class="phone-ico"><svg width="12" height="12" viewBox="0 0 24 24"><path fill="#7fbf3a" d="M6.6 10.8a15 15 0 006.6 6.6l2.2-2.2c.3-.3.7-.4 1-.2 1.1.4 2.3.6 3.6.6.6 0 1 .4 1 1V20c0 .6-.4 1-1 1A17 17 0 013 4c0-.6.4-1 1-1h3.5c.6 0 1 .4 1 1 0 1.3.2 2.5.6 3.6.1.3 0 .7-.2 1z"/></svg></span>(555) 214 7730</div>
</header>

<section class="hero">
  <div class="ph" role="img" aria-label="Arborist climbing a tree with ropes and harness" style="left:0;top:0;width:1200px;height:638px;background:linear-gradient(160deg,#9cc3de,#5d7a3a 55%,#3c4a27)"></div>
  <svg class="abs" style="left:0;top:0" width="1200" height="638"><polygon points="0,0 725,0 375,638 0,638" fill="#7fbf3a"/></svg>
  <div class="hero-copy">
    <div class="eyebrow">WELCOME TO VERDELL TREE CARE</div>
    <h1>VERDELL FOR ALL YOUR<br>TREE CARE NEEDS</h1>
    <p>Serving Lafayette and surrounding areas.</p>
    <div class="btn btn-orange" style="margin-top:30px">Contact Us</div>
  </div>
</section>

<section>
  <svg class="abs" style="left:0;top:780px" width="420" height="523"><polygon points="0,0 420,0 190,523 0,523" fill="#f7a535"/></svg>
  <div class="ph" role="img" aria-label="Arborist in orange shirt working up in a tree" style="left:205px;top:862px;width:320px;height:372px;background:linear-gradient(135deg,#8bb05a,#4d6b2c 60%,#e08a2c)"></div>
  <div class="about-text">
    <h2 class="sec-title">ABOUT VERDELL <span>TREE CARE</span></h2>
    <div class="rule"></div>
    <p>At Verdell Tree Care, we are more than just a tree service company, we are stewards of our beautiful trees. With a passion deeply rooted in arboriculture, we embark on a mission to promote the health, beauty, and safety of your trees and landscapes.</p>
    <p class="quote">Whether it's expert tree trimming to enhance aesthetics, meticulous tree removal to mitigate hazards, or comprehensive tree health assessments to ensure safety, we approach each task with unwavering dedication and attention to detail.</p>
    <div class="btn btn-green" style="margin-top:26px;margin-left:4px">Learn More</div>
  </div>
</section>

<section class="services">
  <div class="center-title" style="top:70px"><h2 class="sec-title">SERVICES <span>PROVIDE</span></h2><div class="rule"></div></div>
  <div class="svc" style="left:118px;top:160px" role="img" aria-label="Pruning shears cutting a branch"><div class="ph" style="inset:0;background:linear-gradient(160deg,#9aa58a,#4d5a3c)"></div><span>TREE PRUNING</span></div>
  <div class="svc featured" style="left:446px;top:160px"><span>TREE REMOVAL</span><p>Lorem ipsum dolor sit amet, consectetur adipiscing elit, sed do eiusmod tempor incididunt ut labore et dolore</p><span class="mini">LEARN MORE</span></div>
  <div class="svc" style="left:773px;top:160px" role="img" aria-label="Young tree being planted in soil"><div class="ph" style="inset:0;background:linear-gradient(160deg,#6fa03e,#5a3f22)"></div><span>TREE PRESERVATION</span></div>
  <div class="svc" style="left:118px;top:402px" role="img" aria-label="Tree stump being ground down"><div class="ph" style="inset:0;background:linear-gradient(160deg,#5e7a3c,#7b5a3a)"></div><span>STUMP GRINDING</span></div>
  <div class="svc" style="left:446px;top:402px" role="img" aria-label="Fallen tree after a storm"><div class="ph" style="inset:0;background:linear-gradient(160deg,#a9b99a,#4d6b30)"></div><span>TREE EMERGENCY SERVICES</span></div>
  <div class="svc" style="left:773px;top:402px" role="img" aria-label="Arborist installing cables in a tree canopy"><div class="ph" style="inset:0;background:linear-gradient(160deg,#90b8d2,#5d6b3a)"></div><span>CABLING &amp; BRACING</span></div>
</section>

<section>
  <div class="center-title" style="top:2150px"><h2 class="sec-title">WHY CHOOSE <span>VERDELL</span></h2><div class="rule"></div></div>
  <svg class="abs" style="left:340px;top:2240px" width="520" height="420"><path d="M20 60 A260 260 0 0 0 500 60" fill="none" stroke="#f5c98a" stroke-width="2"/></svg>
  <div class="ph" role="img" aria-label="Large leafy green tree" style="left:430px;top:2245px;width:330px;height:290px;border-radius:48% 48% 20% 20%;background:radial-gradient(circle at 50% 40%,#5e9a2c,#2e5a18 75%)"></div>
  <div class="feature" style="left:205px;top:2236px;text-align:right"><span>LICENSED AND<br>INSURED</span><div class="dot-ico g"></div></div>
  <div class="feature" style="left:133px;top:2382px;text-align:right"><span>24 HOUR EMERGENCY<br>SERVICES</span><div class="dot-ico o"></div></div>
  <div class="feature" style="left:231px;top:2521px;text-align:right"><span>LOCALLY OWNED<br>&amp; OPERATED</span><div class="dot-ico g"></div></div>
  <div class="feature" style="left:550px;top:2596px;flex-direction:column;gap:8px;text-align:center"><div class="dot-ico o"></div><span>LICENSED ARBORIST<br>ON STAFF</span></div>
  <div class="feature" style="left:746px;top:2528px"><div class="dot-ico g"></div><span>FREE ESTIMATE</span></div>
  <div class="feature" style="left:798px;top:2387px"><div class="dot-ico o"></div><span>SAFETY IS OUR<br>TOP PRIORITY</span></div>
  <div class="feature" style="left:774px;top:2244px"><div class="dot-ico g"></div><span>PROFESSIONAL<br>WORK</span></div>
</section>

<section class="blogs">
  <h2 class="sec-title abs" style="left:103px;top:50px">LATEST <span>BLOGS</span></h2>
  <div class="rule abs" style="left:103px;top:98px"></div>
  <div class="card" style="left:106px;top:144px;width:474px;height:405px">
    <div role="img" aria-label="Chainsaw cutting into a tree trunk" style="height:285px;background:linear-gradient(160deg,#8a8a7a,#5a4a3a)"></div>
    <span class="tag" style="margin-top:-26px;position:absolute;left:24px;top:310px">20 MAY 2024</span>
    <div style="padding:28px 38px 0"><h3>Lorem ipsum dolor sit amet consectetur adipiscing elit sed do eiusmod</h3><span class="more">LEARN MORE</span></div>
  </div>
  <div class="card" style="left:600px;top:144px;width:500px;height:193px;display:flex">
    <div role="img" aria-label="Arborist climbing a tree trunk" style="width:236px;background:linear-gradient(160deg,#9ab07a,#4d5a3c)"></div>
    <div style="padding:40px 26px 0"><span class="tag" style="font-size:9px">20 MAY 2024</span><h3 style="font-size:13px;margin-top:12px">Lorem ipsum dolor sit amet consectetur adipiscing elit sed do eiusmod</h3><span class="more" style="font-size:10px">LEARN MORE</span></div>
  </div>
  <div class="card" style="left:600px;top:357px;width:500px;height:193px;display:flex">
    <div role="img" aria-label="Worker trimming branches with loppers" style="width:236px;background:linear-gradient(160deg,#7fa84a,#3e5a24)"></div>
    <div style="padding:36px 26px 0"><span class="tag" style="font-size:9px">10 MAY 2024</span><h3 style="font-size:13px;margin-top:12px">Lorem ipsum dolor sit amet consectetur adipiscing elit sed do eiusmod</h3><span class="more" style="font-size:10px">LEARN MORE</span></div>
  </div>
</section>

<section class="testi">
  <div class="ph" role="img" aria-label="Faint photo of an arborist in a tree" style="left:0;top:0;width:540px;height:512px;background:linear-gradient(135deg,#f7a535,#f9b85a)"></div>
  <svg class="abs" style="left:0;top:0" width="1200" height="512"><polygon points="540,0 1200,0 1200,512 330,512" fill="#fff"/></svg>
  <div class="abs" style="left:112px;top:150px;color:#fff">
    <h2 style="font-size:28px;font-weight:800;line-height:1.3">WHAT PEOPLE<br>ARE SAYING<br>ABOUT US</h2>
    <div style="font-size:16px;font-weight:700;margin-top:26px">EXLLENT SERVICE</div>
    <div style="font-size:24px;letter-spacing:3px">★★★★★</div>
    <div style="font-size:13px;margin-top:4px">4.8 Rating | 3500 Reviews</div>
  </div>
  <div class="bubble" style="left:388px;top:107px"><div class="q">“</div>“Lorem ipsum dolor sit amet, consectetur adipiscing elit, sed do eiusmod tempor incididunt ut labore et dolore magna aliqua Quis ipsum suspendisse ultrices gravida Risus commodo viverra maecenas ”<b>Daniel Hollis</b><div class="stars">★★★★★</div></div>
  <div class="bubble" style="left:734px;top:107px"><div class="q">“</div>“Lorem ipsum dolor sit amet, consectetur adipiscing elit, sed do eiusmod tempor incididunt ut labore et dolore magna aliqua Quis ipsum suspendisse ultrices gravida Risus commodo viverra maecenas ”<b>Daniel Hollis</b><div class="stars">★★★★★</div></div>
  <div class="bubble" style="left:1112px;top:107px"></div>
  <svg class="abs" style="left:1070px;top:262px" width="20" height="24"><path d="M5 3l10 9-10 9" stroke="#7fbf3a" stroke-width="3" fill="none"/></svg>
</section>

<section>
  <div class="ph" style="left:0;top:3930px;width:1200px;height:585px;background:#f6f5f0"></div>
  <svg class="abs" style="left:0;top:3930px" width="1200" height="585"><polygon points="1035,0 1200,0 1200,585 695,585" fill="#7fbf3a"/></svg>
  <h2 class="sec-title abs" style="left:133px;top:4025px">CONTACT <span>US</span></h2>
  <div class="rule abs" style="left:133px;top:4073px"></div>
  <div class="field" style="top:4108px">First Name*</div>
  <div class="field" style="top:4163px">Email address*</div>
  <div class="field" style="top:4218px">Phone number*</div>
  <div class="field" style="top:4273px;height:86px">Leave Message</div>
  <div class="btn btn-green abs" style="left:135px;top:4379px;font-size:12px;padding:12px 36px">Send Message</div>
  <div class="ph" style="left:612px;top:3968px;width:490px;height:490px;border-radius:50%;background:#3d6b1f"></div>
  <div class="ph" role="img" aria-label="Arborist in orange shirt sitting on a tree limb" style="left:632px;top:3988px;width:450px;height:450px;border-radius:50%;border:6px solid #fff;background:radial-gradient(circle at 50% 50%,#e28a2c,#6a9a3c 40%,#3e5a24)"></div>
</section>

<footer>
  <div class="brand abs" style="left:495px;top:4560px;font-size:28px"><span class="brand-mark" style="width:28px;height:28px"></span>Verdell Tree Care</div>
  <nav class="footer-nav"><span>HOME</span><i></i><span>ABOUT US</span><i></i><span>SERVICES</span><i></i><span>BLOGS</span><i></i><span>REVIEWS</span><i></i><span>CONTACT</span></nav>
  <div class="f-contact" style="left:198px"><span class="dot-ico g" style="width:32px;height:32px"></span>(555) 214-7730</div>
  <div class="f-contact" style="left:432px"><span class="dot-ico g" style="width:32px;height:32px"></span>(555) 386-4412</div>
  <div class="f-contact" style="left:634px"><span class="dot-ico g" style="width:32px;height:32px"></span>hello@verdelltreecare.com</div>
  <div class="abs" style="left:928px;top:4726px;display:flex;gap:14px">
    <span class="dot-ico" style="width:24px;height:24px;background:#555"></span><span class="dot-ico" style="width:24px;height:24px;background:#555"></span><span class="dot-ico" style="width:24px;height:24px;background:var(--green)"></span><span class="dot-ico" style="width:24px;height:24px;background:var(--green)"></span>
  </div>
  <div class="copyright">Copyright © 2024 Verdell Tree Care | All Right Reserved</div>
</footer>

</body>
</html>
```